Social Media Graphics - Oakline Push REVISED

Create 6-7 individual social media graphics (square size) to encourage folks to join our online course called:

The Harvest Ledger Circle
How to Launch a Multi-Million Business From Scratch
Sign Up Today!

IMPORTANT: Make the largest and most prominent text on the graphic be: How to Launch a Multi-Million Business From Scratch

For the color scheme of the graphics, let's try a blue color palette; make sure the graphics appeal to both men and women

Make sure each graphic contains 1 of the 3 pics attached (crop pic as needed); and make sure one of the graphics is all TEXT only.

Target Market(s)

men and women looking to start a business

Industry/Entity Type

Entrepreneurship

Colors
0054AA
0677BA
7BADD7
CADEEF
E8F1F8

Requirements
Must have
• All the text and use the 3 pics provided; one graphic can be all text; Simple, modern design that's easy to read

```html
<!DOCTYPE html>
<html lang="en">
<head>
<meta charset="utf-8">
<title>The Harvest Ledger Circle – Social Graphic</title>
<link href="https://fonts.googleapis.com/css2?family=Anton&family=Oswald:wght@700&display=swap" rel="stylesheet">
<style>
  :root {
    --navy-deep: #003a66;
    --blue-mid: #0060a0;
    --blue-bright: #0a92d8;
    --frame-line: #29a8f0;
    --ink-panel: #1f1d3d;
    --white: #ffffff;
    --photo-light: #9fb4c6;
    --photo-mid: #5f7f9c;
  }
  html, body {
    margin: 0;
    padding: 0;
    width: 1200px;
    height: 1200px;
    overflow: hidden;
  }
  .graphic {
    position: relative;
    width: 1200px;
    height: 1200px;
    overflow: hidden;
    background: linear-gradient(225deg, var(--blue-bright) 0%, var(--blue-mid) 38%, var(--navy-deep) 70%, var(--navy-deep) 100%);
    color: var(--white);
  }
  .frame {
    position: absolute;
    left: 38px;
    top: 38px;
    width: 1123px;
    height: 1123px;
    box-sizing: border-box;
    border: 3px solid var(--frame-line);
  }
  .hero-photo {
    position: absolute;
    left: 363px;
    top: 87px;
    width: 798px;
    height: 560px;
    background: radial-gradient(ellipse 60% 70% at 55% 55%, var(--photo-light) 0%, var(--photo-mid) 55%, rgba(95,127,156,0) 100%);
  }
  .title-badge {
    position: absolute;
    left: 102px;
    top: 85px;
    width: 276px;
    height: 503px;
    box-sizing: border-box;
    padding: 0 18px;
    background: var(--ink-panel);
    border-radius: 26px;
    display: flex;
    flex-direction: column;
    align-items: center;
    justify-content: center;
    font-family: "Anton", sans-serif;
    text-transform: uppercase;
    text-align: center;
    margin: 0;
    font-weight: 400;
  }
  .title-badge span { display: block; white-space: nowrap; }
  .title-badge .word-the { font-size: 86px; line-height: 1.1; }
  .title-badge .word-long { font-size: 62px; line-height: 1.2; letter-spacing: 1px; }
  .headline {
    position: absolute;
    left: 60px;
    top: 640px;
    width: 1080px;
    text-align: center;
    font-family: "Oswald", sans-serif;
    font-weight: 700;
    font-size: 90px;
    line-height: 100px;
    letter-spacing: 1px;
    text-transform: uppercase;
    margin: 0;
  }
  .cta-label {
    position: absolute;
    left: 92px;
    top: 1024px;
    width: 987px;
    display: flex;
    align-items: center;
    gap: 22px;
    font-family: "Oswald", sans-serif;
    font-weight: 700;
    font-size: 62px;
    line-height: 62px;
  }
  .cta-label::before,
  .cta-label::after {
    content: "";
    flex: 1;
    height: 2px;
    background: var(--white);
  }
  .cta-button {
    position: absolute;
    left: 381px;
    top: 1096px;
    width: 437px;
    height: 44px;
    background: var(--ink-panel);
    border-radius: 22px;
    display: flex;
    align-items: center;
    justify-content: center;
    font-family: "Oswald", sans-serif;
    font-weight: 700;
    font-size: 34px;
    letter-spacing: 6px;
    text-transform: uppercase;
  }
</style>
</head>
<body>
  <main class="graphic">
    <div class="frame"></div>
    <div class="hero-photo" role="img" aria-label="Photo of two smiling course hosts on stage, a man in a grey blazer speaking into a microphone and a woman in a blue jacket laughing"></div>
    <p class="title-badge">
      <span class="word-the">The</span>
      <span class="word-long">Harvest</span>
      <span class="word-long">Ledger</span>
      <span class="word-long">Circle</span>
    </p>
    <h1 class="headline">How to Launch a<br>Multi-Million Business<br>From Scratch</h1>
    <div class="cta-label">CTA</div>
    <div class="cta-button">Sign Up Today</div>
  </main>
</body>
</html>
```